Fire Risk Assessment App needs a sleek UI design

I need a sleek, modern but professional design for my 5 page Fire Risk Assessment App. Include gradient background, fire themed colours including reds, yellows, light orange and a touch of black. Design must ooze simplicity and professionalism. This is for the UK market. See attached images and word doc for more information.

Target Market(s)

General public and business owners

Industry/Entity Type

Technology / Fire Safety

Colors
00AB8E
00BBA5
67D7C9
C6EFE9
E9F9F6
59FF00
82FF00
B8FF75
E3FFCB
F4FFEA
FFC000
F8CF3A
FAE287
FDF2CF
FEFAEE
F0912C
F2A743
F7CA91
FBE8D2
FDF5EE
EE7325
F08F49
F5BC92
FAE3D3
FDF4ED
EB3D1F
EC4F4E
F09395
F8D3D4
FCEDEE

```html
<!DOCTYPE html>
<html lang="en">
<head>
<meta charset="utf-8">
<title>Fire Risk Assessment App – Screens</title>
<link rel="stylesheet" href="https://fonts.googleapis.com/css2?family=Montserrat:wght@400;500;600;700&display=swap">
<style>
:root{
  --orange:#F2A743;
  --orange-deep:#F0912C;
  --orange-light:#F7CA91;
  --cream:#FDF5EE;
  --cream-2:#FBE8D2;
  --red:#EB3D1F;
  --red-2:#EC4F4E;
  --green:#00AB8E;
  --green-tick:#3CB54A;
  --green-btn:#A8E6A0;
  --yellow:#FFC000;
  --ink:#1d1d1d;
  --muted:#6b6b6b;
  --icon:#666;
  --white:#ffffff;
}
*{box-sizing:border-box;margin:0;padding:0}
html,body{width:1200px;height:2203px;overflow:hidden}
body{
  font-family:'Montserrat',sans-serif;color:var(--ink);
  background:linear-gradient(180deg,var(--orange) 0%,var(--orange-deep) 100%);
  position:relative;
}
.screen{
  position:absolute;width:450px;height:960px;border-radius:34px;overflow:hidden;
  background:linear-gradient(180deg,#FEFAF6 0%,var(--cream) 60%,var(--cream-2) 100%);
  box-shadow:0 10px 30px rgba(120,50,0,.18);
}
.screen--welcome{left:84px;top:90px}
.screen--dashboard{left:666px;top:90px}
.screen--support{left:84px;top:1152px}
.screen--form{left:666px;top:1152px}
.abs{position:absolute}
.status{position:absolute;top:14px;left:0;right:0;height:24px;font-size:16px;font-weight:500}
.status .time{position:absolute;left:40px;top:0}
.status svg{position:absolute;right:32px;top:2px}
.center-text{position:absolute;left:0;right:0;text-align:center}

/* welcome */
.headline{font-size:23px;font-weight:600;line-height:34px;top:72px}
.hero-art{left:84px;top:162px;width:288px;height:258px;border-radius:6px;
  background:linear-gradient(160deg,#fff 0%,#fbe9d9 100%);box-shadow:0 4px 14px rgba(0,0,0,.1)}
.tagline{font-size:22px;font-weight:600;line-height:34px;top:448px}
.pill-btn{position:absolute;left:72px;width:312px;height:64px;border-radius:32px;
  display:flex;align-items:center;font-size:19px;font-weight:600;color:var(--white)}
.pill-btn .badge{width:56px;height:56px;border-radius:50%;background:var(--white);margin:0 16px 0 4px;
  display:flex;align-items:center;justify-content:center}
.btn-create{top:537px;background:var(--green-btn);color:#E9F9F6}
.btn-login{top:694px;background:var(--red)}
.responsible{top:640px;font-size:21px;font-weight:600}
.endorsed{top:804px;font-size:16px;font-weight:500}
.fingerprint{left:194px;top:846px;width:68px;height:68px;border-radius:50%;background:var(--white);
  box-shadow:0 2px 8px rgba(0,0,0,.15)}

/* dashboard */
.dash-mark{left:68px;top:92px;width:34px;height:34px;border-radius:50%;background:var(--red)}
.dash-title{left:124px;top:90px;font-size:30px;font-weight:700;letter-spacing:.5px}
.dash-sub{top:154px;font-size:18px;font-weight:600}
.start-btn{left:181px;top:191px;width:82px;height:82px;border-radius:50%;background:var(--red)}
.type-img{width:82px;height:82px;border-radius:50%;box-shadow:0 2px 8px rgba(0,0,0,.12)}
.type-img.commercial{left:97px;top:325px;background:radial-gradient(circle,#cfe0ee 0%,#9fb8cc 55%,#fff 56%)}
.type-img.residential{left:262px;top:325px;background:radial-gradient(circle,#f3d3b0 0%,#d9896a 55%,#fff 56%)}
.type-label{top:418px;font-size:18px;font-weight:500;width:160px;text-align:center}
.status-card{position:absolute;left:18px;width:178px;height:48px;background:var(--white);
  box-shadow:0 2px 8px rgba(0,0,0,.1);display:flex;align-items:center;justify-content:space-between;
  padding:0 16px 0 20px;font-size:16px;font-weight:500}
.list-row{position:absolute;left:18px;font-size:11.5px;font-weight:500;text-transform:uppercase;display:flex;align-items:center;gap:12px}
.list-row .dot{width:18px;height:18px;border-radius:50%;border:1.5px solid #bbb}
.tabbar{position:absolute;left:0;right:0;bottom:0;height:64px;background:var(--white);
  display:flex;justify-content:space-around;align-items:center;padding:0 30px}

/* support */
.support-title{left:90px;top:110px;font-size:28px;font-weight:700}
.placeholder{left:37px;top:205px;font-size:17px;color:var(--muted)}
.mic-btn{left:348px;top:189px;width:50px;height:50px;border-radius:50%;background:var(--red);
  display:flex;align-items:center;justify-content:center}
.textarea{left:34px;top:253px;width:378px;height:261px;border:1.5px solid #999;background:rgba(255,255,255,.15)}
.outline-btn{position:absolute;border:2px solid var(--red);border-radius:6px;color:var(--red);
  font-size:18px;font-weight:600;display:flex;align-items:center;justify-content:center;background:var(--white)}

/* form */
.form-title{left:28px;top:106px;font-size:26px;font-weight:700;white-space:nowrap}
.form-meta{left:28px;font-size:20px;font-weight:500;letter-spacing:.3px;line-height:25px}
.progress-label{font-size:13px;color:var(--muted);font-weight:500}
.hazard-icon{left:191px;top:397px;width:66px;height:66px;border-radius:50%;background:var(--ink);
  display:flex;align-items:center;justify-content:center}
.q-num{left:28px;top:474px;font-size:22px;font-weight:600}
.q-text{left:28px;top:510px;width:340px;font-size:22px;line-height:26px;color:#444}
.answer-box{left:36px;top:690px;width:378px;height:54px;background:var(--white);
  box-shadow:0 2px 8px rgba(0,0,0,.12);display:flex;align-items:center;justify-content:center;font-size:16px;font-weight:500}
.photo{left:149px;top:774px;width:152px;height:102px;
  background:linear-gradient(135deg,#3a2a1e 0%,#b55a1c 45%,#FFC000 60%,#6a4a30 100%)}
.save-btn{position:absolute;left:13px;top:822px;width:95px;height:54px;background:var(--red);color:var(--white);
  font-size:17px;font-weight:600;line-height:20px;text-align:center;display:flex;align-items:center;justify-content:center;border-radius:3px}
</style>
</head>
<body>

<!-- Welcome -->
<section class="screen screen--welcome">
  <div class="status"><span class="time">9:30</span>
    <svg width="78" height="18" viewBox="0 0 78 18"><g fill="#111"><rect x="0" y="11" width="3" height="5"/><rect x="5" y="8" width="3" height="8"/><rect x="10" y="5" width="3" height="11"/><rect x="15" y="2" width="3" height="14"/></g><path d="M26 7 q9 -8 18 0 M29 10 q6 -5 12 0" stroke="#111" stroke-width="2" fill="none"/><circle cx="35" cy="13" r="2" fill="#111"/><rect x="52" y="3" width="22" height="11" rx="2" fill="#111"/><rect x="75" y="6" width="2" height="5" fill="#111"/></svg>
  </div>
  <h1 class="center-text headline">The most 'user friendly' Fire Risk<br>Assessment App available. Market</h1>
  <div class="abs hero-art" role="img" aria-label="Stacked fire risk assessment form cards preview"></div>
  <p class="center-text tagline">Quick tap responses and voice<br>activated typing</p>
  <div class="pill-btn btn-create">
    <span class="badge"><svg width="28" height="28" viewBox="0 0 28 28" fill="none" stroke="#8fd98a" stroke-width="2"><circle cx="12" cy="9" r="5"/><path d="M3 24c0-6 4-9 9-9s7 2 8 4"/><path d="M22 17v8M18 21h8"/></svg></span>
    Create a Free account
  </div>
  <p class="center-text responsible">Any Responsible Person can do it.</p>
  <div class="pill-btn btn-login">
    <span class="badge"><svg width="28" height="28" viewBox="0 0 28 28" fill="none" stroke="#EB3D1F" stroke-width="2"><circle cx="11" cy="8" r="5"/><path d="M2 24c0-6 4-9 9-9"/><rect x="15" y="18" width="10" height="7" rx="1"/><path d="M17 18v-3a3 3 0 0 1 6 0v3"/></svg></span>
    Customer Log in
  </div>
  <p class="center-text endorsed">Created and endorsed by British Firefighters</p>
  <div class="abs fingerprint">
    <svg width="68" height="68" viewBox="0 0 68 68" fill="none" stroke="#222" stroke-width="1.8"><path d="M20 30a14 14 0 0 1 28 0v6"/><path d="M24 34a10 10 0 0 1 20 0v6c0 5-2 9-4 12"/><path d="M28 36a6 6 0 0 1 12 0v6c0 4-2 8-5 11"/><path d="M34 38v6c0 4-2 8-5 10"/><path d="M20 36v4c0 5 2 9 5 12"/><path d="M16 26a19 19 0 0 1 36 0"/></svg>
  </div>
</section>

<!-- Dashboard -->
<section class="screen screen--dashboard">
  <div class="status"><span class="time">9:30</span>
    <svg width="78" height="18" viewBox="0 0 78 18"><g fill="#111"><rect x="0" y="11" width="3" height="5"/><rect x="5" y="8" width="3" height="8"/><rect x="10" y="5" width="3" height="11"/><rect x="15" y="2" width="3" height="14"/></g><path d="M26 7 q9 -8 18 0 M29 10 q6 -5 12 0" stroke="#111" stroke-width="2" fill="none"/><circle cx="35" cy="13" r="2" fill="#111"/><rect x="52" y="3" width="22" height="11" rx="2" fill="#111"/><rect x="75" y="6" width="2" height="5" fill="#111"/></svg>
  </div>
  <span class="abs dash-mark"></span>
  <h2 class="abs dash-title">DASHBOARD</h2>
  <p class="center-text dash-sub">Start Fire Risk Assessment</p>
  <svg class="abs" style="left:0;top:270px" width="450" height="60"><path d="M200 4L150 56M244 4L290 56" stroke="#333" stroke-width="1.5" stroke-dasharray="2 4"/></svg>
  <div class="abs start-btn"><svg width="82" height="82"><path d="M41 20v42M20 41h42" stroke="#fff" stroke-width="7"/></svg></div>
  <div class="abs type-img commercial" role="img" aria-label="Commercial office building illustration"></div>
  <div class="abs type-img residential" role="img" aria-label="Residential house illustration"></div>
  <p class="abs type-label" style="left:58px">Commercial</p>
  <p class="abs type-label" style="left:223px">Residential</p>

  <div class="status-card" style="top:476px">Complete
    <svg width="24" height="24"><circle cx="12" cy="12" r="11" fill="#3CB54A"/><path d="M7 12l4 4 6-7" stroke="#fff" stroke-width="2.5" fill="none"/></svg></div>
  <div class="list-row" style="top:549px"><svg width="18" height="16"><rect x="3" y="2" width="10" height="13" fill="#9fb8cc"/><rect x="0" y="13" width="18" height="3" fill="#ccd"/></svg>Ned's Barbershop</div>

  <div class="status-card" style="top:590px">In Progress
    <svg width="28" height="28"><circle cx="14" cy="14" r="11" fill="none" stroke="#3CB54A" stroke-width="2.5" stroke-dasharray="58 12"/></svg></div>
  <div class="list-row" style="top:660px"><span class="dot"></span>Elm Rd School</div>
  <div class="list-row" style="top:689px"><span class="dot"></span>Oakfield Nursing Home</div>

  <div class="status-card" style="top:727px">Purchases
    <svg width="26" height="26" viewBox="0 0 26 26" fill="none" stroke="#3CB54A" stroke-width="1.8"><path d="M4 9h14l1 14H3z"/><path d="M7 9V6a4 4 0 0 1 8 0v3"/><circle cx="19" cy="18" r="5" fill="#fff"/><path d="M17 18l1.5 1.5 3-3"/></svg></div>
  <div class="list-row" style="top:797px"><span class="dot"></span>Residential Fire Risk Assessment</div>
  <div class="list-row" style="top:826px"><span class="dot"></span>Commercial Fire Risk Assessment</div>
  <div class="list-row" style="top:854px"><span class="dot"></span>Commercial Fire Risk Assessment</div>

  <nav class="tabbar">
    <svg width="34" height="32" fill="none" stroke="#666" stroke-width="2.4"><path d="M3 15L17 3l14 12M7 12v17h20V12"/><rect x="14" y="19" width="6" height="10" fill="#666" stroke="none"/></svg>
    <svg width="36" height="26"><rect x="1" y="2" width="34" height="22" rx="3" fill="#666"/><rect x="1" y="8" width="34" height="4" fill="#fff"/></svg>
    <svg width="32" height="30"><path d="M2 2h28v18H12l-8 7v-7H2z" fill="#666"/><path d="M8 9h16M8 14h10" stroke="#fff" stroke-width="2"/></svg>
    <svg width="32" height="34" fill="none" stroke="#666" stroke-width="2"><rect x="4" y="2" width="18" height="30"/><circle cx="17" cy="17" r="1.5" fill="#666"/><path d="M22 17h9M27 13l4 4-4 4"/></svg>
  </nav>
</section>

<!-- Technical Support -->
<section class="screen screen--support">
  <div class="status"><span class="time">9:30</span>
    <svg width="78" height="18" viewBox="0 0 78 18"><g fill="#111"><rect x="0" y="11" width="3" height="5"/><rect x="5" y="8" width="3" height="8"/><rect x="10" y="5" width="3" height="11"/><rect x="15" y="2" width="3" height="14"/></g><path d="M26 7 q9 -8 18 0 M29 10 q6 -5 12 0" stroke="#111" stroke-width="2" fill="none"/><circle cx="35" cy="13" r="2" fill="#111"/><rect x="52" y="3" width="22" height="11" rx="2" fill="#111"/><rect x="75" y="6" width="2" height="5" fill="#111"/></svg>
  </div>
  <svg class="abs" style="left:37px;top:114px" width="40" height="38"><path d="M2 2h36v24H14l-10 9v-9H2z" fill="#F0912C"/><path d="M9 11h22M9 18h14" stroke="#fff" stroke-width="3"/></svg>
  <h2 class="abs support-title">Technical Support</h2>
  <p class="abs placeholder">Type / record you response here.</p>
  <div class="abs mic-btn"><svg width="22" height="28" fill="none" stroke="#fff" stroke-width="2.4"><rect x="7" y="1" width="8" height="16" rx="4" fill="#fff"/><path d="M3 12a8 8 0 0 0 16 0M11 20v6"/></svg></div>
  <div class="abs textarea"></div>
  <div class="outline-btn" style="left:320px;top:534px;width:90px;height:44px">Send</div>
  <nav class="tabbar">
    <svg width="34" height="32" fill="none" stroke="#666" stroke-width="2.4"><path d="M3 15L17 3l14 12M7 12v17h20V12"/><rect x="14" y="19" width="6" height="10" fill="#666" stroke="none"/></svg>
    <svg width="36" height="26"><rect x="1" y="2" width="34" height="22" rx="3" fill="#666"/><rect x="1" y="8" width="34" height="4" fill="#fff"/></svg>
    <svg width="32" height="30"><path d="M2 2h28v18H12l-8 7v-7H2z" fill="#F0912C"/><path d="M8 9h16M8 14h10" stroke="#fff" stroke-width="2"/></svg>
    <svg width="32" height="34" fill="none" stroke="#666" stroke-width="2"><rect x="4" y="2" width="18" height="30"/><circle cx="17" cy="17" r="1.5" fill="#666"/><path d="M22 17h9M27 13l4 4-4 4"/></svg>
  </nav>
</section>

<!-- Fire Risk Assessment Form -->
<section class="screen screen--form">
  <div class="status"><span class="time">9:30</span>
    <svg width="78" height="18" viewBox="0 0 78 18"><g fill="#111"><rect x="0" y="11" width="3" height="5"/><rect x="5" y="8" width="3" height="8"/><rect x="10" y="5" width="3" height="11"/><rect x="15" y="2" width="3" height="14"/></g><path d="M26 7 q9 -8 18 0 M29 10 q6 -5 12 0" stroke="#111" stroke-width="2" fill="none"/><circle cx="35" cy="13" r="2" fill="#111"/><rect x="52" y="3" width="22" height="11" rx="2" fill="#111"/><rect x="75" y="6" width="2" height="5" fill="#111"/></svg>
  </div>
  <h2 class="abs form-title">Fire Risk Assessment Form</h2>
  <p class="abs form-meta" style="top:182px">FIRE RISK ASSESSMENT</p>
  <p class="abs form-meta" style="top:218px">FIRE HAZARDS</p>
  <p class="abs form-meta" style="top:276px;font-size:18px">SECTION 7-00/30-00</p>
  <p class="abs form-meta" style="top:324px">ELECTRONIC SOURCES<br>OF IGNITION</p>
  <p class="abs progress-label" style="left:300px;top:190px">Section Progress</p>
  <svg class="abs" style="left:328px;top:216px" width="60" height="60"><circle cx="30" cy="30" r="27" fill="#fff" stroke="#eee" stroke-width="3"/><circle cx="30" cy="30" r="27" fill="none" stroke="#3CB54A" stroke-width="3" stroke-dasharray="70 100" transform="rotate(-90 30 30)"/></svg>
  <p class="abs progress-label" style="left:285px;top:290px">Assessment Progress</p>
  <svg class="abs" style="left:328px;top:316px" width="60" height="60"><circle cx="30" cy="30" r="27" fill="#fff" stroke="#eee" stroke-width="3"/><circle cx="30" cy="30" r="27" fill="none" stroke="#3CB54A" stroke-width="3" stroke-dasharray="30 200" transform="rotate(-90 30 30)"/></svg>
  <div class="abs hazard-icon"><svg width="28" height="38"><path d="M18 1L3 22h10l-4 15 16-22H15z" fill="#FFC000"/></svg></div>
  <p class="abs q-num">Q:7:01</p>
  <p class="abs q-text">Are reasonable measures taken to prevent fires of electrical origin?</p>
  <svg class="abs" style="left:60px;top:612px" width="340" height="60">
    <circle cx="30" cy="29" r="26" fill="none" stroke="#3CB54A" stroke-width="3"/><path d="M19 29l8 8 14-15" stroke="#3CB54A" stroke-width="3" fill="none"/>
    <circle cx="100" cy="29" r="26" fill="none" stroke="#EB3D1F" stroke-width="3"/><path d="M90 19l20 20M110 19l-20 20" stroke="#EB3D1F" stroke-width="3"/>
    <circle cx="169" cy="29" r="26" fill="none" stroke="#F0912C" stroke-width="3"/><path d="M157 29h24" stroke="#F0912C" stroke-width="3"/>
    <path d="M222 16h10l4-6h14l4 6h10v28h-42z" fill="#111"/><circle cx="243" cy="30" r="9" fill="#fff"/><circle cx="243" cy="30" r="6" fill="#111"/>
    <rect x="300" y="4" width="16" height="30" rx="8" fill="#111"/><path d="M294 24a14 14 0 0 0 28 0M308 38v12" stroke="#111" stroke-width="3" fill="none"/>
  </svg>
  <div class="abs answer-box">No,electric sockets are overloaded.</div>
  <div class="abs photo" role="img" aria-label="Photo of a kitchen fire hazard"></div>
  <div class="save-btn">Save<br>+ Close</div>
  <div class="outline-btn" style="left:348px;top:822px;width:89px;height:46px">Next</div>
  <nav class="tabbar">
    <svg width="34" height="32" fill="none" stroke="#666" stroke-width="2.4"><path d="M3 15L17 3l14 12M7 12v17h20V12"/><rect x="14" y="19" width="6" height="10" fill="#666" stroke="none"/></svg>
    <svg width="36" height="26"><rect x="1" y="2" width="34" height="22" rx="3" fill="#666"/><rect x="1" y="8" width="34" height="4" fill="#fff"/></svg>
    <svg width="32" height="30"><path d="M2 2h28v18H12l-8 7v-7H2z" fill="#666"/><path d="M8 9h16M8 14h10" stroke="#fff" stroke-width="2"/></svg>
    <svg width="32" height="34" fill="none" stroke="#666" stroke-width="2"><rect x="4" y="2" width="18" height="30"/><circle cx="17" cy="17" r="1.5" fill="#666"/><path d="M22 17h9M27 13l4 4-4 4"/></svg>
  </nav>
</section>

</body>
</html>
```